Redesign Canvas Art E-Commerce Website

Help! I hired a couple of companies on Brisklo.com to build and design an e-commerce website for me. After three long and painful months, I have one that I believe is functional on the back-end, but aesthetically on the front end is a mess.

We are a small family business that will take your digital photo and manipulate it into a digitally created oil, watercolor or impressionist style pieces of artwork that we print on museum quality, gallery grade canvas and ship to the customer, ready to hang.

We are looking to create an e-commerce website where a customer can choose their art style, upload a photo, choose their canvas size and orientation (horizontal or vertical) and checkout. Within 48 hours, we will send them back a proof of their newly created, customized artwork for them to approve or not approve. If they approve, we print, package and ship them the product. If they do not approve, we offer unlimited revisions until they are happy.

As I mentioned, the back end functionality is already there, just need design help. No coding required

Here is a link to the development page that they created: https://plumwickstudio.com/development/

As you can see, it looks off...doesnt line up properly, wasted space, weird font. Feel free to either correct the homepage they created or design an entirely new page. I am attaching some examples of before and after photos of artwork for reference. I also think the testimonials page and shop page can use a little style. The content is there and accurate, it just doesn't look pretty. Please keep in mind that our customers will probably not be very tech savvy. The customers will probably be sending us pics of kids, grandkids, pets, family portraits, vacation photos, etc.

Here is one of our competitors - www.gildavantry.com
Their website looks clean and inviting.

Thank you in advance! Im looking forward to seeing the results. I am including our logo in the attachments (I do not have it in a vector file, just a jpeg)

Target Market(s)

Non tech-savvy indiduals, 30-70 years old

Industry/Entity Type

Please look at https://plumwickstudio.com/development/ to see various pages and what the other designers did

Number of Pages Required

1 page

Requirements
Must have
• Verbiage on pages leave "as is" but feel free to change styles. Would like to keep existing four categories on homepage
Nice to have
• Warm and inviting homepage that evokes emotion

```html
<!DOCTYPE html>
<html lang="en">
<head>
<meta charset="utf-8">
<title>Plumwick Studio – Turn Your Digital Photos Into Wall Art</title>
<link rel="stylesheet" href="https://fonts.googleapis.com/css2?family=Poppins:ital,wght@0,400;0,500;0,600;0,700;1,500&display=swap">
<style>
:root{
  --orange:#ee5a24;
  --blue:#1da1c8;
  --yellow:#fdd43a;
  --ink:#333333;
  --body:#4a4a4a;
  --soft:#f4f4f4;
  --footer:#161616;
  --footer-bar:#0c0c0c;
  --white:#ffffff;
}
*{box-sizing:border-box;margin:0;padding:0}
html,body{width:1200px;height:4182px;overflow:hidden}
body{position:relative;font-family:"Poppins",sans-serif;color:var(--ink);background:var(--white)}
.abs{position:absolute}

/* header */
.site-header{left:0;top:0;width:1200px;height:122px;background:var(--white)}
.brand{left:76px;top:44px;display:flex;align-items:center;gap:10px;font-weight:700;font-size:24px;color:var(--ink)}
.brand-dot{width:28px;height:28px;border-radius:50%;background:var(--orange)}
.nav{top:58px;font-size:16px;font-weight:500;color:var(--ink)}
.cart{left:1096px;top:59px}
.cart-count{left:1110px;top:53px;width:16px;height:16px;border-radius:50%;background:var(--orange);color:#fff;font-size:10px;text-align:center;line-height:16px}

/* hero */
.hero{left:0;top:122px;width:1200px;height:739px;
  background:
    radial-gradient(ellipse 300px 260px at 60% 35%,rgba(230,205,190,.55),transparent 70%),
    radial-gradient(ellipse 260px 220px at 78% 58%,rgba(30,36,60,.85),transparent 70%),
    radial-gradient(ellipse 420px 200px at 20% 40%,rgba(60,110,40,.9),transparent 75%),
    radial-gradient(ellipse 380px 240px at 85% 20%,rgba(70,120,45,.9),transparent 75%),
    radial-gradient(ellipse 260px 180px at 42% 18%,rgba(150,40,30,.7),transparent 75%),
    radial-gradient(ellipse 240px 170px at 24% 82%,rgba(50,90,40,.95),transparent 75%),
    linear-gradient(180deg,#3b2a22 0%,#4a3a2e 60%,#8a7a6a 78%,#6e6258 100%)}
.hero-shade{left:0;top:122px;width:1200px;height:739px;background:rgba(0,0,0,.18)}
.hero-title{left:0;top:338px;width:1200px;text-align:center;font-size:82px;font-weight:700;color:#fff;line-height:1.2}
.hero-sub{left:0;top:436px;width:1200px;text-align:center;font-size:46px;font-style:italic;font-weight:500;color:#fff;line-height:53px}
.btn{background:var(--orange);color:#fff;font-weight:600;display:flex;align-items:center;justify-content:center}
.hero-btn{left:525px;top:573px;width:149px;height:57px;font-size:16px}

/* sections */
.section-title{left:0;width:1200px;text-align:center;font-size:48px;font-weight:700;color:var(--ink);line-height:56px}
.category{overflow:hidden}
.category-label{position:absolute;left:0;bottom:0;width:100%;height:110px;background:linear-gradient(transparent,rgba(0,0,0,.75));color:#fff;font-weight:700;font-size:39px;padding:0 18px 12px;display:flex;align-items:flex-end}

.about-band{left:0;top:1780px;width:422px;height:539px;background:var(--yellow)}
.about-photo{left:62px;top:1824px;width:524px;height:451px;
  background:
    radial-gradient(ellipse 110px 140px at 60% 30%,#e7c3aa,transparent 70%),
    radial-gradient(ellipse 170px 110px at 28% 78%,#f2f2ea,transparent 72%),
    radial-gradient(ellipse 90px 80px at 85% 15%,#f4f0e4,transparent 72%),
    radial-gradient(ellipse 140px 160px at 80% 80%,#e9e5dc,transparent 72%),
    linear-gradient(135deg,#2d2620,#5b4a3a 50%,#3a3028)}
.about-title{left:614px;top:1770px;font-size:48px;font-weight:700;color:var(--ink)}
.about-lead{left:614px;top:1836px;width:520px;font-size:17px;font-weight:500;color:var(--blue);line-height:30px}
.about-body{left:614px;top:1903px;width:520px;font-size:15.5px;color:var(--body);line-height:27.6px}
.about-btn{left:617px;top:2262px;width:150px;height:57px;font-size:16px}

.why{left:0;top:2395px;width:1200px;height:605px;background:var(--soft)}
.why-card{top:2572px;width:328px;height:345px;background:#fff;border-radius:14px;text-align:center;padding:30px 22px 0}
.why-card svg{display:block;margin:0 auto 10px}
.why-card h3{font-size:21px;font-weight:600;color:var(--blue);line-height:34px;margin-bottom:8px}
.why-card p{font-size:15px;color:var(--body);line-height:27.6px}

/* footer */
.footer{left:0;top:3708px;width:1200px;height:417px;background:var(--footer)}
.footer-bar{left:0;top:4125px;width:1200px;height:57px;background:var(--footer-bar);color:#ddd;font-size:14px;text-align:center;line-height:57px}
.footer-brand{left:76px;top:3878px;display:flex;align-items:center;gap:10px;font-weight:700;font-size:24px;color:#fff}
.footer-heading{font-size:18px;font-weight:600;color:#fff}
.sitemap{left:362px;top:3762px}
.sitemap ul{list-style:none;margin-top:8px}
.sitemap li{font-size:15px;color:#ddd;line-height:34px}
.newsletter{left:614px;top:3762px;width:512px}
.newsletter p{font-size:15px;color:#ddd;margin-top:8px}
.signup{left:614px;top:3854px;width:512px;height:61px;display:flex}
.signup-field{flex:1;background:#2b2b2b;border:1px solid #444;color:#ccc;font-size:15px;padding-left:18px;display:flex;align-items:center}
.signup-btn{width:90px;font-size:16px}
.follow{left:614px;top:3952px}
.social{left:614px;top:4004px;display:flex;gap:22px}
.social span{width:21px;height:21px;border:2px solid #fff;border-radius:4px}
</style>
</head>
<body>

<header class="site-header abs">
  <div class="brand abs"><span class="brand-dot"></span>Plumwick Studio</div>
  <span class="nav abs" style="left:375px">Home</span>
  <span class="nav abs" style="left:460px">Shop</span>
  <span class="nav abs" style="left:538px">Testimonials</span>
  <span class="nav abs" style="left:679px">About Us</span>
  <span class="nav abs" style="left:788px">FAQs</span>
  <span class="nav abs" style="left:866px">Contact Us</span>
  <span class="nav abs" style="left:992px">My Orders</span>
  <svg class="cart abs" width="20" height="18" viewBox="0 0 20 18"><path d="M1 6h18l-2 11H3z" fill="#333"/><path d="M6 6l4-5 4 5" stroke="#333" stroke-width="2" fill="none"/></svg>
  <span class="cart-count abs">0</span>
</header>

<section>
  <div class="hero abs" role="img" aria-label="Oil-painted canvas of a couple embracing among greenery, with a phone showing the original photo"></div>
  <div class="hero-shade abs"></div>
  <h1 class="hero-title abs">Plumwick Studio</h1>
  <p class="hero-sub abs">Turn Your Digital Photos Into<br>One of a Kind Wall Art</p>
  <div class="btn hero-btn abs">GET STARTED</div>
</section>

<h2 class="section-title abs" style="top:933px">Categories</h2>
<div class="category abs" style="left:75px;top:1031px;width:511px;height:304px;background:radial-gradient(ellipse 120px 130px at 62% 40%,#d8c8b8,transparent 70%),radial-gradient(ellipse 90px 90px at 80% 70%,#2a2c3a,transparent 70%),radial-gradient(ellipse 140px 100px at 20% 30%,#8a2a1e,transparent 72%),radial-gradient(ellipse 160px 120px at 25% 80%,#3d6a26,transparent 72%),linear-gradient(135deg,#2e5520,#4c7a2c 50%,#2a4a1a)" role="img" aria-label="Oil style portrait of a wedding couple"><span class="category-label">Oil</span></div>
<div class="category abs" style="left:614px;top:1031px;width:513px;height:304px;background:radial-gradient(ellipse 140px 110px at 60% 35%,#e9b9a0,transparent 72%),radial-gradient(ellipse 160px 100px at 25% 60%,#e6b49c,transparent 72%),linear-gradient(135deg,#fbf6f2,#f3e2d6 50%,#fdfbf9)" role="img" aria-label="Watercolor style portrait of a mother and baby"><span class="category-label">Watercolor</span></div>
<div class="category abs" style="left:75px;top:1366px;width:511px;height:303px;background:radial-gradient(ellipse 160px 140px at 30% 55%,#3a2616,transparent 72%),radial-gradient(ellipse 170px 130px at 72% 45%,#d9893a,transparent 72%),radial-gradient(ellipse 120px 90px at 20% 20%,#e8e2d8,transparent 72%),linear-gradient(135deg,#cfc6b8,#8a5a30 50%,#b87030)" role="img" aria-label="Impressionist style portrait of a dog and a cat"><span class="category-label">Impressionist</span></div>
<div class="category abs" style="left:614px;top:1366px;width:513px;height:303px;background:radial-gradient(ellipse 110px 120px at 35% 35%,#efe9e2,transparent 72%),radial-gradient(ellipse 110px 110px at 72% 35%,#e2b896,transparent 72%),radial-gradient(ellipse 140px 80px at 80% 85%,#2aa0b8,transparent 72%),linear-gradient(135deg,#4e6e30,#7a5236 50%,#5a8a3a)" role="img" aria-label="Digital photo of two children eating ice cream"><span class="category-label">Digital Photo</span></div>

<section>
  <div class="about-band abs"></div>
  <div class="about-photo abs" role="img" aria-label="Smiling bride holding a white bouquet"></div>
  <h2 class="about-title abs">About Us</h2>
  <p class="about-lead abs">At Plumwick Studio, we take your digital photo and turn it into a one-of-a-kind piece of artwork!</p>
  <div class="about-body abs">
    <p style="margin-bottom:6px">The process couldn't be any easier. Simply upload your photo, choose your art style and size, and let our team of skilled digital artists do the rest. Do you want to put your digital photo on canvas without an art style? No problem! Just choose the "Digital Photo/Retouching" category and upload your photo.</p>
    <p>We can print your photo "as is" or do some minor retouching (e.g. remove objects, enhance colors, lighten photo, etc).</p>
    <p>You will receive a proof in your email to approve within 1-2 days. Once approved, your customized artwork will be transferred to canvas and shipped from our design studio in Florida.</p>
    <p>Plumwick Studio art makes a great gift for just about any special occasion.</p>
  </div>
  <div class="btn about-btn abs">Read More</div>
</section>

<section>
  <div class="why abs"></div>
  <h2 class="section-title abs" style="top:2466px">Why Us?</h2>
  <div class="why-card abs" style="left:75px">
    <svg width="80" height="80" viewBox="0 0 80 80" fill="none" stroke="#ee5a24" stroke-width="2.5"><rect x="8" y="28" width="50" height="46" rx="4"/><circle cx="36" cy="20" r="10"/><path d="M32 30h8"/><circle cx="36" cy="52" r="8"/><path d="M66 10v58l4 6 4-6V10z"/></svg>
    <h3>Your Idea Your<br>Design</h3>
    <p>Each art piece is customized for you! You choose your size, orientation and art style. Makes a perfect gift!!!</p>
  </div>
  <div class="why-card abs" style="left:437px">
    <svg width="112" height="80" viewBox="0 0 112 80" fill="none" stroke="#ee5a24" stroke-width="2.5"><circle cx="44" cy="26" r="20"/><path d="M44 14v12l8 6"/><path d="M20 48h58l14 10v12H20z"/><circle cx="36" cy="72" r="6"/><circle cx="78" cy="72" r="6"/><path d="M2 54h12M6 62h10"/></svg>
    <h3>Fast Shipping</h3>
    <p>Your artwork is printed and shipped in the USA! We offer fast turnaround with transit times typically 3-7 days. Free tracking with each order!!</p>
  </div>
  <div class="why-card abs" style="left:799px">
    <svg width="80" height="80" viewBox="0 0 80 80" fill="none" stroke="#ee5a24" stroke-width="2.5"><path d="M40 4l3 7h7l-6 4 2 7-6-4-6 4 2-7-6-4h7z"/><path d="M14 14l2 4h4l-3 3 1 4-4-2-4 2 1-4-3-3h4z"/><path d="M66 14l2 4h4l-3 3 1 4-4-2-4 2 1-4-3-3h4z"/><circle cx="40" cy="52" r="24"/><path d="M30 50h6v16h-6zM36 52l6-10c3 0 4 2 3 6h8v12c0 3-2 6-5 6H36"/></svg>
    <h3>High Quality</h3>
    <p>We've put a lot of effort ensuring your artwork is of the highest quality. Each piece is printed on the highest quality, gallery grade canvas. It is ready to hang upon arrival.!</p>
  </div>
</section>

<section>
  <h2 class="section-title abs" style="top:3054px">From Photo To Museum<br>Quality Canvas Art</h2>
  <div class="abs" style="left:75px;top:3207px;width:341px;height:202px;background:radial-gradient(ellipse 70px 80px at 62% 35%,#e2bea6,transparent 72%),radial-gradient(ellipse 120px 60px at 30% 85%,#eeeee6,transparent 72%),radial-gradient(ellipse 60px 50px at 85% 15%,#f0ece2,transparent 72%),linear-gradient(135deg,#241e18,#4a3c30 55%,#2c241e)" role="img" aria-label="Bride with bouquet rendered as canvas art"></div>
  <div class="abs" style="left:75px;top:3427px;width:341px;height:199px;background:radial-gradient(ellipse 60px 80px at 65% 40%,#5a7fa6,transparent 72%),radial-gradient(ellipse 50px 60px at 35% 55%,#d7dbe0,transparent 72%),radial-gradient(ellipse 180px 60px at 50% 90%,#c4d2dc,transparent 72%),linear-gradient(135deg,#4e6a32,#8a9a5a 50%,#3e5a2a)" role="img" aria-label="Child and father walking on a path, painted style"></div>
  <div class="abs" style="left:430px;top:3207px;width:341px;height:419px;background:radial-gradient(ellipse 70px 80px at 68% 22%,#d9b8a0,transparent 72%),radial-gradient(ellipse 70px 80px at 38% 42%,#d8b29a,transparent 72%),radial-gradient(ellipse 120px 110px at 58% 40%,#4e6e4e,transparent 72%),radial-gradient(ellipse 150px 140px at 45% 80%,#7cb0d6,transparent 72%),linear-gradient(180deg,#f2f3f0,#e8ece8)" role="img" aria-label="Watercolor of an older couple laughing together"></div>
  <div class="abs" style="left:786px;top:3207px;width:341px;height:419px;background:radial-gradient(ellipse 120px 160px at 45% 45%,#7a3a16,transparent 72%),radial-gradient(ellipse 90px 80px at 70% 60%,#c46a22,transparent 72%),radial-gradient(ellipse 60px 70px at 70% 12%,#1a1e2a,transparent 72%),linear-gradient(135deg,#6aaee0,#3a86c8 50%,#9ccbe8)" role="img" aria-label="Impressionist painting of a horse and rider jumping"></div>
</section>

<footer>
  <div class="footer abs"></div>
  <div class="footer-brand abs"><span class="brand-dot"></span>Plumwick Studio</div>
  <div class="sitemap abs">
    <div class="footer-heading">Site Map</div>
    <ul><li>Home</li><li>Shop</li><li>Testimonials</li><li>About Us</li><li>FAQs</li><li>Contact Us</li><li>My Orders</li></ul>
  </div>
  <div class="newsletter abs">
    <div class="footer-heading">Newsletter Sign Up</div>
    <p>Excepteur sint occaecat cupidatat non proident laboris nisi.</p>
  </div>
  <div class="signup abs"><div class="signup-field">Email Address</div><div class="btn signup-btn">Sign Up</div></div>
  <div class="follow footer-heading abs">Follow Us</div>
  <div class="social abs" aria-label="Social media links"><span></span><span></span><span></span><span></span><span></span></div>
  <div class="footer-bar abs">Copyright © 2023 CompanyName . All rights reserved.</div>
</footer>

</body>
</html>
```